Business Identity Stationary

Already have the logo which is in the attached files so only need the Business STationary
1) Double Sided Business Card
2) Letterhead
3) Presentation folder with business card holder on inside cover
4) WIth compliments slip
See information for business cards, letterhead and presentation folder below.

This should be a simply job using a logo we already had designed along with a little device. I suggest using the device off center and perhaps lower in the corner in an abstract way. Also the logo device could be used as a watermark for the letterhead. The designer who created the logo presented something that I think works well for a business card. The front of the double sided business card could have the name logo small for the website address and only use the Lime device on the front. Then on the back could be the name Barrow Advisory logo.

Please note that for the business card the black and lime green background do look good. Also please think of using the lime device separately in an unusual way.

It has been brought to my attention that.my budget was far to low. Hopefully this.will attract you to the project. 

The parent company of Barrow Advisory is TallHeron holdings. I have uploaded a file of the Tall Heron business card I really like. Perhaps use this business card as a guide to the type of modern and clean style I am looking for. It also works to have the Barrow Advisroy and Tall Heron similar.

Reason: Still haven't received anything exactly right.

Industry/Entity Type

Business

Font styles to use
Sans Serif

Colors
9bcb3c
000000
5c5c5c
add136
cadf82
eaf2cf
f9fbf2
1b1b1b
757575

Requirements
Must have
• 1) Double Sided Business Card
Marta Kellendorf
Director
Tel: +505 8264 3170
Email: mk@barrowadvisory-example.com
Website: www.barrowadvisory-example.com

Frederick Kellendorf
Director
Tel: +505 8264 3172
Email: fk@barrowadvisory-example.com

Lucia Brenes Otaduy
Director
Tel: 8642 1093
Email: lbo@barrowadvisory-example.com

2) Letterhead
Logo
Lime Logo Device
Website Address: www.barrowadvisory-example.com
Small print on bottom: Barrow Advisory a Tall Heron Holding Company SA. RUC J0487000239518

3) Presentation Folder
Traditional Presentation folder with inside front cover spot for the insertion of business card.

4) With Compliments slip

```html
<!DOCTYPE html>
<html lang="en">
<head>
<meta charset="utf-8">
<title>Barrow Advisory – With Compliments</title>
<link href="https://fonts.googleapis.com/css2?family=PT+Sans:wght@400&display=swap" rel="stylesheet">
<style>
  :root {
    --lime: #add136;
    --ink: #1b1b1b;
    --paper-light: #3c3c3c;
    --paper-dark: #0e0e0e;
    --text-light: #f4f4f4;
    --mark: #9a9a9a;
  }
  html, body {
    margin: 0;
    padding: 0;
    overflow: hidden;
    background: #ffffff;
  }
  .slip {
    position: relative;
    width: 1200px;
    height: 552px;
    overflow: hidden;
    background: radial-gradient(ellipse 70% 80% at 55% 45%, var(--paper-light) 0%, #222 55%, var(--paper-dark) 100%);
    font-family: "PT Sans", sans-serif;
    color: var(--text-light);
  }
  .crop-marks {
    position: absolute;
    inset: 0;
  }
  .brand {
    position: absolute;
    left: 120px;
    top: 62px;
    margin: 0;
    font-size: 44px;
    font-weight: 400;
    line-height: 1;
    color: var(--text-light);
    letter-spacing: 1px;
  }
  .greeting {
    position: absolute;
    left: 120px;
    top: 240px;
    margin: 0;
    font-size: 32px;
    font-weight: 400;
    letter-spacing: 1px;
    text-transform: uppercase;
    white-space: nowrap;
  }
  .message {
    position: absolute;
    left: 573px;
    top: 110px;
    margin: 0;
    font-size: 25px;
    line-height: 34.5px;
    text-transform: uppercase;
    letter-spacing: 0;
  }
  .message-line {
    display: block;
    white-space: nowrap;
  }
  .web-band {
    position: absolute;
    left: 0;
    top: 417px;
    width: 921px;
    height: 88px;
  }
  .web-address {
    position: absolute;
    left: 133px;
    top: 417px;
    height: 88px;
    margin: 0;
    display: flex;
    align-items: center;
    font-size: 33px;
    letter-spacing: 1px;
    color: var(--ink);
    text-transform: uppercase;
    white-space: nowrap;
  }
</style>
</head>
<body>
  <main class="slip">
    <svg class="crop-marks" width="1200" height="552" aria-hidden="true">
      <g stroke="var(--mark)" stroke-width="1.5">
        <line x1="0" y1="37" x2="25" y2="37"/>
        <line x1="37" y1="0" x2="37" y2="25"/>
        <line x1="1175" y1="37" x2="1200" y2="37"/>
        <line x1="1163" y1="0" x2="1163" y2="25"/>
        <line x1="0" y1="515" x2="25" y2="515"/>
        <line x1="37" y1="527" x2="37" y2="552"/>
        <line x1="1175" y1="515" x2="1200" y2="515"/>
        <line x1="1163" y1="527" x2="1163" y2="552"/>
      </g>
    </svg>

    <h1 class="brand">Barrow Advisory</h1>

    <p class="greeting">With compliments</p>

    <p class="message">
      <span class="message-line">Qua tu etiam inprudens utebare non</span>
      <span class="message-line">numquam. Restatis igitur vos; ita cum ea</span>
      <span class="message-line">volunt retinere, quae superiori sententiae</span>
      <span class="message-line">conveniunt, in Aristonem incidunt;</span>
      <span class="message-line">Dicet pro me ipsa virtus nec dubitabit isti</span>
      <span class="message-line">vestro beato M.</span>
    </p>

    <svg class="web-band" width="921" height="88" aria-hidden="true">
      <rect x="0" y="0" width="780" height="88" fill="var(--lime)"/>
      <rect x="785" y="0" width="64" height="88" fill="var(--lime)"/>
      <rect x="855" y="0" width="38" height="88" fill="var(--lime)"/>
      <rect x="899" y="0" width="22" height="88" fill="var(--lime)"/>
    </svg>
    <p class="web-address">www.barrowadvisory-example.com</p>
  </main>
</body>
</html>
```